Design a cover that embodies the concept of healing by Walking Out of Shadows

Subtitle: How to use tapping, applied kinesiology, and Chinese medicine to heal your body, free your mind and live in peace.

Tapping (Emotional Freedom Technique) is a modern mix of psychology and Chinese medicine that helps people to release the emotions they have inside that are contributing to the depression and anxiety they feel. Applied kinesiology or muscle testing is a biofeedback tool which helps to extract information from the body that can help people to profoundly heal. It can be used to determine whether heavy metals, heavy chemicals, food sensitivities or pathogens are causing the body problems. It can also be used to determine which supplements can help someone heal. This tool also can be used to identify emotions and memories that are also causing someone problems. Lastly, Chinese medicine uses food therapy, herbal formulas, meditation, tai chi (meditative movement), cupping and other tools to help people to be free of depression. This book is written to be information but also details my own personal journey of how I was able to heal from 11 years of heavy depression through the use of these tools.

The heart of the book is about emotional release, emotional freedom and emotional healing. You can surrender, release or let go of emotions and feel better very quickly. This certainly was my experience.

I would like the front and back cover to each be 8.5" x 5.5". I still have to get an ISBN number for the back page as well. Here is the text that I would like on the back cover for now: Millions of people feel the pain, loneliness, and agony of anxiety and depression every day. Many turn to Western medicine in the hopes that a pill will ease the pain and make the problem go away. Oftentimes, this only makes matters worse and doesn’t address the root cause. No one should have to struggle like this when natural answers exist that can address the physical, energetic, emotional, or spiritual causes of anxiety and depression. For 11 long years, Dr. Mervin personally struggled with heavy depression until he discovered answers that helped him to completely heal. Walking Out of Shadows is a guide that will help you discover - The two root physical causes of depression and exactly what to do to start healing today - How the negative emotions we have stored within from trauma and bad experiences can drive depression - Tools from Chinese medicine, applied kinesiology, and tapping to help you free your mind and live in peace - An actionable plan to help you let go of the pain, suffering, and negative emotions from your past Whether you feel depressed and anxious or know someone who struggles with these issues, Walking Out of Shadows will transform how you think about depression and will give you the tools to heal so that you can be free and live in peace. Dr. Mervin Holloway is a board-certified acupuncture physician licensed in the state of Florida. He received his training at the Marlow Institute of Restorative Health. He also graduated with a master’s degree in counseling and psychology from Cedarbrook School of Ministry. His mission is to help people transform their health and improve the quality of their life naturally. He lives in Orlando, FL where he runs a holistic medical clinic called Brightpath Wellness Center. www.drmervinholloway.example Instagram: drmervinholloway Facebook: brightpathwellnesscenter

Target Market(s)

Those who suffer from depression and anxiety and want to heal naturally

Industry/Entity Type

Health And Wellness

Requirements
Must have
• My picture should be small and go on the back cover next to the information about me. The front cover would be all graphical. Thank you. On the front cover my name should be posted as "Dr. Mervin Holloway, AP, MA"

```html
<!DOCTYPE html>
<html lang="en">
<head>
<meta charset="UTF-8">
<title>Walking Out of Shadows — Cover</title>
<link rel="stylesheet" href="https://fonts.googleapis.com/css2?family=Fjalla+One&display=swap">
<style>
  :root {
    --backdrop: #b1a8a8;
    --cover-black: #070707;
    --spine-black: #262626;
    --spine-edge: #8fc9c4;
    --title-white: #ffffff;
    --subtitle-yellow: #e4e694;
    --rule-grey: #9a9a9a;
    --bat-grey: #3a3a3a;
  }
  * { margin: 0; padding: 0; box-sizing: border-box; }
  html, body {
    width: 1200px;
    height: 1000px;
    overflow: hidden;
    background: var(--backdrop);
    font-family: "Fjalla One", "Oswald", sans-serif;
    font-weight: 400;
  }
  .canvas {
    position: relative;
    width: 1200px;
    height: 1000px;
  }

  /* Front cover */
  .front-cover {
    position: absolute;
    left: 183px;
    top: 86px;
    width: 548px;
    height: 834px;
    background: var(--cover-black);
    overflow: hidden;
  }
  .cover-art {
    position: absolute;
    left: 11px;
    top: 17px;
    width: 525px;
    height: 514px;
    background:
      radial-gradient(ellipse 40% 35% at 25% 28%, rgba(40,90,220,0.95), rgba(40,90,220,0) 70%),
      radial-gradient(ellipse 38% 40% at 30% 55%, rgba(20,190,200,0.9), rgba(20,190,200,0) 72%),
      radial-gradient(ellipse 45% 40% at 50% 72%, rgba(110,215,40,0.95), rgba(110,215,40,0) 72%),
      radial-gradient(ellipse 40% 38% at 72% 25%, rgba(235,70,20,0.95), rgba(235,70,20,0) 70%),
      radial-gradient(ellipse 38% 40% at 75% 52%, rgba(245,210,30,0.95), rgba(245,210,30,0) 72%),
      radial-gradient(ellipse 30% 30% at 62% 40%, rgba(250,150,30,0.85), rgba(250,150,30,0) 72%);
    -webkit-mask-image: radial-gradient(ellipse 52% 50% at 50% 50%, #000 60%, transparent 100%);
    mask-image: radial-gradient(ellipse 52% 50% at 50% 50%, #000 60%, transparent 100%);
  }
  .cover-title {
    font-weight: 400;
    color: var(--title-white);
  }
  .cover-title span {
    position: absolute;
    left: 0;
    width: 548px;
    text-align: center;
    line-height: 1;
    white-space: nowrap;
  }
  .cover-title .title-lead {
    top: 478px;
    font-size: 40px;
  }
  .cover-title .title-main {
    top: 528px;
    font-size: 84px;
    letter-spacing: 0.5px;
  }
  .cover-author {
    position: absolute;
    right: 48px;
    top: 616px;
    color: var(--title-white);
    font-size: 17px;
    line-height: 1;
    white-space: nowrap;
  }
  .cover-bats {
    position: absolute;
    left: 168px;
    top: 645px;
    width: 205px;
    height: 52px;
    background: radial-gradient(ellipse 50% 40% at 50% 50%, rgba(58,58,58,0.8), rgba(58,58,58,0) 80%);
  }
  .cover-subtitle {
    position: absolute;
    left: 0;
    top: 750px;
    width: 548px;
    text-align: center;
    color: var(--subtitle-yellow);
    font-size: 19px;
    line-height: 23px;
  }

  /* Spine */
  .spine {
    position: absolute;
    left: 999px;
    top: 80px;
    width: 55px;
    height: 842px;
    background: var(--spine-black);
    border-right: 4px solid var(--spine-edge);
    overflow: hidden;
  }
  .spine-title, .spine-subtitle, .spine-author {
    position: absolute;
    writing-mode: vertical-rl;
    white-space: nowrap;
  }
  .spine-title {
    left: 6px;
    top: 8px;
    font-weight: 400;
    color: var(--title-white);
    line-height: 40px;
  }
  .spine-title .title-lead { font-size: 18px; }
  .spine-title .title-main { font-size: 34px; }
  .spine-rule {
    position: absolute;
    left: 10px;
    width: 30px;
    height: 1px;
    background: var(--rule-grey);
  }
  .spine-rule.upper { top: 285px; }
  .spine-rule.lower { top: 659px; }
  .spine-subtitle {
    left: 12px;
    top: 306px;
    color: var(--subtitle-yellow);
    font-size: 13px;
    line-height: 15px;
  }
  .spine-author {
    left: 12px;
    top: 672px;
    color: var(--title-white);
    font-size: 14px;
    line-height: 28px;
  }
</style>
</head>
<body>
<main class="canvas">
  <section class="front-cover">
    <div class="cover-art" role="img" aria-label="Illustration of a face formed from flowing rainbow brush strokes in blue, green, yellow and orange, with small flowers in the hair"></div>
    <h1 class="cover-title">
      <span class="title-lead">Walking OUT OF</span>
      <span class="title-main">Shadows</span>
    </h1>
    <p class="cover-author">DR. MERVIN HOLLOWAY, AP, MA</p>
    <div class="cover-bats" role="img" aria-label="Faint silhouettes of bats flying away into the dark"></div>
    <p class="cover-subtitle">How to use tapping, applied kinesiology, and Chinese medicine<br>to heal your body, free your mind and live in peace.</p>
  </section>

  <aside class="spine">
    <h2 class="spine-title"><span class="title-lead">Walking OUT OF </span><span class="title-main">Shadows</span></h2>
    <div class="spine-rule upper"></div>
    <p class="spine-subtitle">How to use tapping, applied kinesiology, and Chinese medicine<br>to heal your body, free your mind and live in peace.</p>
    <div class="spine-rule lower"></div>
    <p class="spine-author">DR. MERVIN HOLLOWAY, AP, MA</p>
  </aside>
</main>
</body>
</html>
```